Need business card with a logo for a hearing aid sales and audiology business. We have two Hearing Instrument Specialists and one Audiologist on staff. Over 25 years in business. Locally owned and operated. Financing available. Most insurances accepted.

Summit Audio Wellness LLC
48730 W Larchmont, Suite 7
Spokane, WA 99281
509-617-2084
www.summitaudiowell.example

Manager
Tobias Kerrell HIS COHC
License #71829046

Target Market(s)

50yr old + people with a hearing loss.

Industry/Entity Type

Business

Contact Information for Business Card

48730 W Larchmont, Suite 7
Spokane, WA 99281
509-617-2084
www.summitaudiowell.example

Manager
Tobias Kerrell HIS COHC
NLVE #71829046

Font styles to use
Serif
Sans Serif

Requirements
Must have
• Business name, Tobias's name and title(s) and contact information, License #, web address

```html
<!DOCTYPE html>
<html lang="en">
<head>
<meta charset="utf-8">
<title>Summit Audio Wellness – Business Card</title>
<link rel="stylesheet" href="https://fonts.googleapis.com/css2?family=Josefin+Slab:wght@400;600&display=swap">
<style>
  :root {
    --backdrop: #d9d9d9;
    --lime: #9ccc2c;
    --ink: #231f20;
    --text-dark: #2a2a2a;
    --white: #ffffff;
  }
  * { margin: 0; padding: 0; box-sizing: border-box; }
  html, body { width: 1200px; height: 800px; overflow: hidden; }
  body {
    background: var(--backdrop);
    font-family: "Josefin Slab", Georgia, serif;
    position: relative;
  }
  .business-card {
    position: absolute;
    left: 110px; top: 120px;
    width: 980px; height: 560px;
    border-radius: 44px;
    overflow: hidden;
  }
  .card-shapes { position: absolute; inset: 0; }
  .contact-block {
    position: absolute;
    left: 80px; top: 0;
    color: var(--text-dark);
  }
  .person-name {
    position: absolute; top: 118px; white-space: nowrap;
    font-size: 36px; color: var(--white);
  }
  .person-credentials { font-size: 19px; color: var(--text-dark); margin-left: 6px; }
  .person-title { position: absolute; top: 164px; font-size: 25px; white-space: nowrap; }
  .license-number { position: absolute; top: 202px; left: 12px; font-size: 25px; white-space: nowrap; }
  .divider {
    position: absolute; top: 248px; left: 0;
    width: 350px; height: 2px; background: var(--text-dark);
  }
  .address { position: absolute; top: 298px; left: 40px; font-size: 26px; line-height: 36px; white-space: nowrap; font-style: normal; }
  .contact-line {
    position: absolute; left: 60px;
    display: flex; align-items: center; gap: 12px;
    font-size: 27px; white-space: nowrap;
  }
  .contact-line svg { width: 26px; height: 26px; }
  .phone { top: 410px; }
  .website { top: 456px; }
  .brand-lockup {
    position: absolute;
    left: 690px; top: 200px; width: 290px;
    display: flex; flex-direction: column; align-items: center; gap: 22px;
  }
  .brand-dot { width: 60px; height: 60px; border-radius: 50%; background: var(--lime); }
  .brand-name {
    color: var(--white);
    font-size: 30px; font-weight: 400;
    letter-spacing: 3px; text-transform: uppercase;
    text-align: center; line-height: 36px;
  }
</style>
</head>
<body>
  <div class="business-card">
    <svg class="card-shapes" viewBox="0 0 980 560" width="980" height="560" aria-hidden="true">
      <rect width="980" height="560" fill="var(--lime)"/>
      <path class="dark-panel" d="M560 0 C640 150 690 410 790 560 L980 560 L980 0 Z" fill="var(--ink)"/>
      <path class="accent-stripe" d="M488 0 L512 0 C575 140 630 330 672 448 C610 320 540 150 488 0 Z" fill="var(--ink)"/>
    </svg>

    <div class="contact-block">
      <p class="person-name">Tobias Kerrell<span class="person-credentials">HIS COHC</span></p>
      <p class="person-title">Manager</p>
      <p class="license-number">NLVE #71829046</p>
      <div class="divider"></div>
      <address class="address">48730 W Larchmont, Suite 7<br>Spokane, WA 99281</address>
      <p class="contact-line phone">
        <svg viewBox="0 0 26 26" aria-hidden="true"><circle cx="13" cy="13" r="11.5" fill="none" stroke="var(--white)" stroke-width="2"/><path d="M9 7.5c-1.5 1-1.6 3 .4 6s4.4 5 6.2 4.4l1.2-1.3-2.3-2-1.2.8c-1-.6-2.2-2-2.6-3.2l1-1-1.5-2.6z" fill="var(--white)"/></svg>
        509-617-2084
      </p>
      <p class="contact-line website">
        <svg viewBox="0 0 26 26" aria-hidden="true"><circle cx="13" cy="13" r="11.5" fill="var(--white)"/><path d="M6 9c2 0 3 1 3 3s2 2 2 4-1 3-1 5M15 4c0 2 1 3 3 3s3 2 2 4M14 14c2 0 4 1 4 3s-1 3-2 4" fill="none" stroke="var(--lime)" stroke-width="1.8"/></svg>
        www.summitaudiowell.example
      </p>
    </div>

    <div class="brand-lockup">
      <div class="brand-dot"></div>
      <p class="brand-name">Summit Audio<br>Wellness</p>
    </div>
  </div>
</body>
</html>
```